Design NEW business card

We would like a business card using the colour deep red wine or dark navy blue textured background (patterned or not, open to suggestions) with a high gloss debossed rose gold/copper RM Roland Mercer Jewellery business name (Provided). I have included images for your review we would like to keep our currently logo and business name on the front but you can change the layout and positioning. For the back of the card we are open to all suggestions/variations.
Business
Use our current RM Roland Mercer Jewellery logo (Provided image)

```html
<!DOCTYPE html>
<html lang="en">
<head>
<meta charset="utf-8">
<title>Roland Mercer Jewellery – Business Card</title>
<link rel="stylesheet" href="https://fonts.googleapis.com/css2?family=Source+Sans+3:wght@400;600&display=swap">
<style>
  :root {
    --backdrop: #3a3532;
    --wine: #5e2631;
    --wine-deep: #52202a;
    --rose-gold: #c99a7e;
    --copper: #b07a52;
    --silver: #d9cfcf;
    --ink-light: #f3ecea;
  }
  * { box-sizing: border-box; margin: 0; padding: 0; }
  html, body {
    width: 1200px;
    height: 864px;
    overflow: hidden;
    background: var(--backdrop);
    font-family: "Source Sans 3", "Myriad Pro", sans-serif;
  }
  .stage {
    position: relative;
    width: 1200px;
    height: 864px;
  }
  .card {
    position: absolute;
    width: 540px;
    height: 309px;
    background: linear-gradient(135deg, var(--wine) 0%, var(--wine-deep) 100%);
    box-shadow: 0 10px 24px rgba(0,0,0,0.35);
  }
  .card--front { left: 60px; top: 80px; }
  .card--back { left: 600px; top: 470px; }

  .brand {
    position: absolute;
    left: 70px;
    top: 92px;
    display: flex;
    align-items: center;
    gap: 14px;
  }
  .brand__dot {
    width: 14px;
    height: 14px;
    border-radius: 50%;
    background: var(--silver);
  }
  .brand__name {
    color: var(--silver);
    font-weight: 600;
    font-size: 24px;
    letter-spacing: 4px;
    text-transform: uppercase;
    line-height: 1.2;
  }
  .front__web {
    position: absolute;
    left: 70px;
    top: 180px;
    color: var(--rose-gold);
    font-size: 15px;
    letter-spacing: 4px;
    opacity: 0.85;
  }

  .contact {
    position: absolute;
    left: 150px;
    top: 96px;
    text-align: left;
    color: var(--ink-light);
    font-size: 15px;
    line-height: 1.45;
  }
  .contact__name {
    font-weight: 600;
    color: var(--copper);
    font-size: 16px;
  }
  .contact__role {
    color: var(--silver);
    font-weight: 400;
  }
  .contact__web {
    font-weight: 600;
    letter-spacing: 3px;
    margin-top: 2px;
  }
</style>
</head>
<body>
  <main class="stage">
    <section class="card card--front" aria-label="Card front">
      <div class="brand">
        <span class="brand__dot"></span>
        <span class="brand__name">Roland Mercer<br>Jewellery</span>
      </div>
      <p class="front__web">www.rolandmercer.com</p>
    </section>

    <section class="card card--back" aria-label="Card back">
      <div class="contact">
        <p><span class="contact__name">DANIEL HART</span> <span class="contact__role">- CEO/FOUNDER</span></p>
        <p>4120 Willow Crest Road, Juneau, Alaska 99801</p>
        <p>P. 555 210 4471 M. 555 318 2290</p>
        <p>F. 555 406 7712 E. hello@rolandmercer.com</p>
        <p class="contact__web">www.rolandmercer.com</p>
      </div>
    </section>
  </main>
</body>
</html>
```